Wealth Education Business Needs Sharp Business Card Design

We need a business card design for a recently launched investor education business called Harbor Crest.

The final design should promote security, empowerment, self improvement and financial gain. The card will ideally promote the stature of the business.

For more information and colours please visit harborcrest.com.au

Target Market(s)

Corporate executives and high net worth individuals

Industry/Entity Type

Education

Contact Information for Business Card

```html
<!DOCTYPE html>
<html lang="en">
<head>
<meta charset="utf-8">
<title>Harbor Crest — Business Card</title>
<link href="https://fonts.googleapis.com/css2?family=Exo+2:wght@400;500;700&display=swap" rel="stylesheet">
<style>
  :root {
    --page: #e9e7e3;
    --white: #ffffff;
    --ink: #2a2a2c;
    --slate: #3d3d40;
    --slate-dark: #333336;
    --sky: #1e9bd7;
    --light: #f4f4f4;
  }
  * { box-sizing: border-box; margin: 0; padding: 0; }
  html, body {
    width: 1200px;
    height: 1018px;
    overflow: hidden;
    background: var(--page);
    font-family: "Exo 2", sans-serif;
  }
  .sheet {
    width: 1200px;
    height: 1018px;
    display: flex;
    flex-direction: column;
    align-items: center;
    justify-content: center;
    gap: 18px;
  }
  .card {
    position: relative;
    width: 840px;
    height: 480px;
    overflow: hidden;
    box-shadow: 0 6px 18px rgba(0,0,0,0.18);
  }

  /* Front */
  .card-front { background: var(--white); }
  .brand-area {
    position: absolute;
    left: 0; top: 0;
    width: 100%; height: 230px;
    display: flex;
    align-items: center;
    padding-left: 64px;
    gap: 22px;
  }
  .brand-dot {
    width: 34px; height: 34px;
    border-radius: 50%;
    background: var(--sky);
  }
  .brand-name {
    font-size: 46px;
    font-weight: 500;
    letter-spacing: 11px;
    color: var(--ink);
    text-transform: uppercase;
  }
  .contact-band {
    position: absolute;
    left: 0; top: 230px;
    width: 100%; height: 104px;
    background: var(--slate);
    display: grid;
    grid-template-columns: 230px 1fr;
    grid-template-rows: 1fr 1fr;
    align-items: center;
    padding: 14px 64px;
    color: var(--light);
    font-size: 17px;
    letter-spacing: 0.5px;
  }
  .contact-item { display: flex; align-items: center; gap: 10px; }
  .contact-item svg { width: 16px; height: 16px; flex: none; }
  .identity-band {
    position: absolute;
    left: 0; top: 334px;
    width: 100%; height: 146px;
    background: var(--sky);
    color: var(--white);
    display: flex;
    justify-content: space-between;
    align-items: flex-end;
    padding: 0 56px 34px 64px;
  }
  .identity-band::before {
    content: "";
    position: absolute;
    right: 0; top: 0;
    width: 0; height: 0;
    border-top: 146px solid var(--slate);
    border-left: 110px solid transparent;
    opacity: 0;
  }
  .person-name {
    font-size: 30px;
    font-weight: 700;
    letter-spacing: 1px;
    text-transform: uppercase;
    line-height: 1.1;
  }
  .person-role {
    font-size: 17px;
    font-weight: 400;
    letter-spacing: 2px;
    text-transform: uppercase;
    margin-top: 4px;
  }
  .address {
    text-align: right;
    font-size: 19px;
    line-height: 1.45;
    letter-spacing: 1px;
  }

  /* Back */
  .card-back { background: var(--slate); }
  .card-back svg { display: block; }
</style>
</head>
<body>
<main class="sheet">

  <section class="card card-front" aria-label="Business card front">
    <div class="brand-area">
      <span class="brand-dot" aria-hidden="true"></span>
      <span class="brand-name">Harbor Crest</span>
    </div>

    <div class="contact-band">
      <div class="contact-item">
        <svg viewBox="0 0 16 16" aria-hidden="true"><path fill="currentColor" d="M3.5 1.5l2.5 0 1 3.5-1.6 1.1a8 8 0 0 0 4.5 4.5L11 9l3.5 1v2.5c0 .8-.7 1.5-1.5 1.5C7 14 2 9 2 3c0-.8.7-1.5 1.5-1.5z"/></svg>
        <span>013 482 5570</span>
      </div>
      <div class="contact-item">
        <svg viewBox="0 0 16 16" aria-hidden="true"><rect x="1.5" y="3.5" width="13" height="9" fill="none" stroke="currentColor" stroke-width="1.4"/><path d="M1.5 3.5l6.5 5 6.5-5" fill="none" stroke="currentColor" stroke-width="1.4"/></svg>
        <span>hello@harborcrest.com.au</span>
      </div>
      <div class="contact-item">
        <svg viewBox="0 0 16 16" aria-hidden="true"><rect x="4" y="1.5" width="8" height="13" rx="1.2" fill="none" stroke="currentColor" stroke-width="1.4"/><circle cx="8" cy="12.2" r="0.9" fill="currentColor"/></svg>
        <span>013 482 5570</span>
      </div>
      <div class="contact-item">
        <svg viewBox="0 0 16 16" aria-hidden="true"><circle cx="8" cy="8" r="6.5" fill="none" stroke="currentColor" stroke-width="1.3"/><ellipse cx="8" cy="8" rx="2.8" ry="6.5" fill="none" stroke="currentColor" stroke-width="1.1"/><path d="M1.5 8h13M2.5 4.8h11M2.5 11.2h11" stroke="currentColor" stroke-width="1"/></svg>
        <span>www.harborcrest.com.au</span>
      </div>
    </div>

    <div class="identity-band">
      <div class="person">
        <p class="person-name">Daniel Reeve</p>
        <p class="person-role">General Manager</p>
      </div>
      <p class="address">42 Quayside Road,<br>Level 3 Pier Street</p>
    </div>
  </section>

  <section class="card card-back" aria-label="Business card back">
    <svg width="840" height="480" viewBox="0 0 840 480" aria-hidden="true">
      <rect class="back-field" width="840" height="480" fill="var(--slate)"/>
      <polygon class="back-corner" points="0,0 150,0 0,70" fill="var(--sky)"/>
      <rect class="back-band" x="0" y="150" width="840" height="80" fill="var(--sky)"/>
      <rect class="back-stem" x="430" y="230" width="96" height="250" fill="var(--sky)"/>
      <rect class="back-block" x="526" y="230" width="314" height="250" fill="var(--slate-dark)"/>
    </svg>
  </section>

</main>
</body>
</html>
```